Company or website name
- The Steadfast Haulers and Storage
- Links to the website
- Pinecrestcartage.com
- Describe your company and organization and target audience
- Residential and commercial moving and relocation service that needs a website redesign.
- The design should have the following
- I NEED THE WEBSITE TO BE SIMPLE AND STRAIGHT TO THE POINT...MAIN CONCERN IS THAT THEY FILL OUT INFORMATION TO GET QUOTE. SITE EXAMPLE THAT I LIKE IS ( WWW.MYDORVALS.COM) https://www.corvellfreight.com/

```html
<!DOCTYPE html>
<html lang="en">
<head>
<meta charset="utf-8">
<title>Steadfast Haulers and Storage – Get Moved</title>
<link href="https://fonts.googleapis.com/css2?family=Roboto:ital,wght@0,300;0,400;0,500;0,700;1,400&display=swap" rel="stylesheet">
<style>
:root{
  --brand:#ef3b55;
  --brand-soft:#e94b60;
  --bar:#262626;
  --ink:#222;
  --muted:#c8c8c8;
  --tab-off:#ececec;
  --tab-line:#dcdcdc;
  --field-line:#9c9c9c;
  --error:#e8202a;
  --white:#fff;
}
*{box-sizing:border-box;margin:0;padding:0}
html,body{width:1200px;height:626px;overflow:hidden;background:var(--white);font-family:'Roboto',sans-serif;color:var(--ink)}
.page{position:relative;width:1200px;height:626px}

.announce{position:absolute;left:0;top:0;width:1200px;height:57px;background:var(--bar);color:var(--white)}
.announce-icon{position:absolute;left:216px;top:15px}
.announce-text{position:absolute;left:262px;top:17px;font-size:16.5px;font-weight:400;letter-spacing:.1px}
.announce-text strong{font-weight:700}
.announce-btn{position:absolute;left:805px;top:10px;width:179px;height:37px;background:var(--white);border-radius:3px;color:var(--ink);font-weight:500;font-size:13.5px;display:flex;align-items:center;justify-content:center;gap:4px}
.announce-close{position:absolute;left:1159px;top:19px;font-size:14px;font-weight:500}

.hero{position:absolute;left:0;top:57px;width:676px;height:569px;background:linear-gradient(160deg,#f24a62 0%,#ef3b55 45%,#e5344e 100%)}
.hero-photo{position:absolute;inset:0;background:radial-gradient(ellipse at 60% 65%,rgba(200,30,55,.35),rgba(239,59,85,0) 70%)}
.brand{position:absolute;left:75px;top:44px;display:flex;align-items:center;gap:7px;color:var(--white);white-space:nowrap}
.brand-mark{width:11px;height:11px;background:var(--white)}
.brand-name{font-size:16px;font-weight:700;letter-spacing:.2px;line-height:19px}
.nav{position:absolute;top:48px;left:345px;color:var(--white);font-size:12.5px}
.nav a{position:absolute;white-space:nowrap;color:inherit;text-decoration:none}
.headline{position:absolute;left:168px;top:246px;width:349px;height:66px;border-top:1px solid rgba(255,255,255,.9);border-bottom:1px solid rgba(255,255,255,.9)}
.headline h1{position:absolute;left:-8px;top:-1px;font-size:57px;font-weight:700;color:var(--white);letter-spacing:-1px;line-height:66px;white-space:nowrap}

.quote{position:absolute;left:700px;top:80px;width:427px}
.tabs{display:flex;gap:6px}
.tab{width:138px;height:93px;border:1px solid var(--tab-line);background:var(--tab-off);color:var(--muted);display:flex;flex-direction:column;align-items:center;justify-content:flex-end;padding-bottom:16px;gap:6px;font-size:13.5px;font-weight:500;border-radius:2px}
.tab.is-active{background:var(--brand);border-color:var(--brand);color:var(--white)}
.field{position:absolute;width:209px}
.field label{display:block;font-size:12px;color:var(--ink);height:19px}
.field .input{height:39px;border:1px solid var(--field-line);font-size:10.5px;padding:0 13px;display:flex;align-items:center;color:var(--ink)}
.hint{font-size:10px;margin-top:9px}
.error{font-size:10px;color:var(--error);font-weight:300;margin-top:8px}
.hint+.error{margin-top:5px}
.actions{position:absolute;top:441px;left:0;display:flex;gap:8px}
.btn{width:209px;height:40px;display:flex;align-items:center;justify-content:center;font-size:16.5px;font-weight:500;border-radius:2px}
.btn-primary{background:var(--brand-soft);color:var(--white)}
.btn-outline{border:2px solid var(--brand);color:var(--brand)}
.note{position:absolute;top:508px;left:0;width:427px;text-align:center;font-size:10.5px;font-style:italic;color:#333}
</style>
</head>
<body>
<div class="page">
  <div class="announce">
    <svg class="announce-icon" width="30" height="24" viewBox="0 0 30 24" fill="none" stroke="#fff" stroke-width="1.4">
      <path d="M2 9h5l10-6v18L7 15H2z"/><path d="M5 15l2 7h3l-1-7"/><path d="M21 8l4-3M22 12h5M21 16l4 3"/>
    </svg>
    <p class="announce-text"><strong>ANNOUNCEMENT:</strong> Please read our latest updates on COVID-19</p>
    <div class="announce-btn">Read More
      <svg width="13" height="8" viewBox="0 0 13 8"><path d="M0 4h11M8 1l3 3-3 3" stroke="#222" stroke-width="1.5" fill="none"/></svg>
    </div>
    <span class="announce-close">X</span>
  </div>

  <section class="hero">
    <div class="hero-photo" role="img" aria-label="Photo of a branded moving truck trailer under a cloudy sky, tinted red"></div>
    <div class="brand"><span class="brand-mark"></span><span class="brand-name">Steadfast Haulers &amp; Storage</span></div>
    <nav class="nav">
      <a style="left:0">SERVICES &#8964;</a>
      <a style="left:84px">FAQS</a>
      <a style="left:143px">BLOG</a>
      <a style="left:202px">CONTACT</a>
    </nav>
    <div class="headline"><h1>GET MOVED.</h1></div>
  </section>

  <form class="quote">
    <div class="tabs">
      <div class="tab is-active">
        <svg width="34" height="34" viewBox="0 0 34 34" fill="none" stroke="#fff" stroke-width="1.6"><path d="M3 17L17 4l14 13"/><path d="M7 14v17h20V14"/><path d="M14 31v-9h6v9"/></svg>
        Residential</div>
      <div class="tab">
        <svg width="40" height="34" viewBox="0 0 40 34" fill="none" stroke="#bbb" stroke-width="1.4"><rect x="3" y="5" width="20" height="28"/><rect x="23" y="14" width="14" height="19"/><path d="M3 3h20M7 10h4M14 10h4M7 16h4M14 16h4M7 22h4M14 22h4M27 19h3M32 19h2M27 25h3M32 25h2"/></svg>
        Office</div>
      <div class="tab">
        <svg width="56" height="34" viewBox="0 0 56 34" fill="none" stroke="#bbb" stroke-width="1.3"><path d="M4 32l8-14h34l8 14z"/><circle cx="12" cy="14" r="4"/><path d="M12 22l-3-5M12 22l3-5"/><circle cx="40" cy="6" r="3"/><path d="M40 13l-2-4M40 13l2-4"/><path d="M14 26h10l4-6h12" stroke-dasharray="2 2"/></svg>
        Relocation</div>
    </div>

    <div class="field" style="left:0;top:130px"><label>I am moving from... *</label><div class="input">Zip Code</div><p class="error">This field is required.</p></div>
    <div class="field" style="left:217px;top:130px"><label>I am moving to...*</label><div class="input">Zip Code</div></div>
    <div class="field" style="left:0;top:230px"><label>Moving Date*</label><div class="input"></div><p class="hint">Date Format: MM slash DD slash YYYY</p><p class="error">This field is required.</p></div>
    <div class="field" style="left:217px;top:230px"><label>Your Full Name (First and Last) *</label><div class="input"></div><p class="error">This field is required.</p></div>
    <div class="field" style="left:0;top:349px"><label>Your E-Mail Address *</label><div class="input"></div><p class="error">This field is required.</p></div>
    <div class="field" style="left:217px;top:349px"><label>Your Phone Number *</label><div class="input"></div><p class="error">This field is required.</p></div>

    <div class="actions">
      <div class="btn btn-primary">FREE QUOTE</div>
      <div class="btn btn-outline">MAKE A RESERVATION</div>
    </div>
    <p class="note">A Harlow Moving Solutions agent will be e-mailing you a quote in 24 hours or less</p>
  </form>
</div>
</body>
</html>
```